Food Hall in San Clemente, CA by the Pacific Ocean that has 15 vendors and 2 bars

We need a web page design that highlights our food hall in San Clemente, CA. The name of the food hall is Calloway Food Hall. Inside of the food hall there are 15 different vendors and 2 bars. The place has a beautiful patio and it is by Pacific Ocean. Most of the vendors are local to San Clemente area. The highly anticipated location is opening during the summer of 2025. Website should have a dropdown menu for the different vendors that are in the food hall and people should be able to click to their respective business website. The website should also include link to our social media channels and also a link to provide comments and subscribe for the mailing list.
Target Market(s)
Mostly residents in the San Clemente, CA and surrounding areas. Couples, families and tourist alike that are looking for an exceptional dining experience that everyone can find something they like.
Industry/Entity Type
Restaurants
Coding
Number of Pages Required
Font styles to use
Look and feel

```html
<!DOCTYPE html>
<html lang="en">
<head>
<meta charset="utf-8">
<title>Calloway Food Hall — Where Local Flavor Meets Ocean Air</title>
<link rel="stylesheet" href="https://fonts.googleapis.com/css2?family=Fraunces:opsz,wght@9..144,400;9..144,500&family=Work+Sans:wght@400;500;600;700&display=swap">
<style>
:root{
  --ocean:#0a78c8;
  --ocean-deep:#0658a6;
  --ocean-light:#1f9be0;
  --sand:#e8c9a0;
  --sand-pale:#f6e7d2;
  --orange:#f7a13b;
  --ink:#2b2b2b;
  --ink-soft:#5b5346;
  --white:#ffffff;
}
*{box-sizing:border-box;margin:0;padding:0}
html,body{width:1200px;height:3635px;overflow:hidden}
body{position:relative;background:var(--sand);font-family:"Work Sans",sans-serif;color:var(--ink)}
.abs{position:absolute}
.serif{font-family:"Fraunces",serif;font-weight:400}
a{color:inherit;text-decoration:none}
.btn{position:absolute;display:flex;align-items:center;justify-content:center;border-radius:20px;font-size:14px;font-weight:600}
.btn-white{background:var(--white);color:var(--ocean-deep)}
.btn-blue{background:linear-gradient(180deg,var(--ocean-light),var(--ocean-deep));color:var(--white)}

/* header */
.site-header{left:0;top:0;width:1200px;height:82px;background:linear-gradient(90deg,#0c5fa6,#1584cc 50%,#0c5fa6);border-bottom:3px solid var(--orange);z-index:5}
.brand{left:113px;top:25px;display:flex;align-items:center;gap:10px;font-family:"Work Sans",sans-serif;font-size:24px;font-weight:600;color:var(--white);white-space:nowrap}
.brand-mark{width:14px;height:14px;border-radius:50%;background:var(--orange)}
.nav{left:448px;top:30px;display:flex;gap:35px;font-size:14.5px;color:var(--white)}
.nav .active{color:var(--orange)}
.caret{display:inline-block;width:6px;height:6px;border-right:1.5px solid #fff;border-bottom:1.5px solid #fff;transform:rotate(45deg);margin:0 0 3px 6px}
.reserve{left:904px;top:23px;width:183px;height:34px;background:var(--orange);color:var(--ocean-deep);border-radius:18px}

/* hero */
.hero{left:0;top:82px;width:1200px;height:520px;background:radial-gradient(ellipse at 30% 20%,#b8703e 0%,#5b3523 35%,#2a1c18 70%),linear-gradient(#3a2a26,#1e1612)}
.hero-kicker{left:0;width:1200px;top:228px;text-align:center;font-size:23px;color:var(--white);font-weight:500}
.hero-title{left:0;width:1200px;top:262px;text-align:center;font-size:56px;line-height:58px;color:var(--white)}

/* story */
.story-img{left:113px;top:642px;width:452px;height:388px;border-radius:48% 52% 44% 56%/55% 45% 55% 45%;background:radial-gradient(circle at 50% 45%,#c98a4a,#6d5848 55%,#3c3a3a)}
.section-title{font-size:42px;color:var(--ocean)}
.story-text{left:640px;top:734px;width:448px;font-size:15px;line-height:29px;color:var(--ink-soft);text-align:justify}
.story-text p+p{margin-top:17px}

/* vendors */
.center{left:0;width:1200px;text-align:center}
.sub{font-size:15.5px;color:var(--ink)}
.card{top:1231px;width:311px;height:381px;background:var(--white);border-radius:20px;overflow:hidden}
.card.featured{border:2px solid var(--ocean-light)}
.card-photo{width:100%;height:216px}
.card-badge{position:absolute;left:20px;top:0;width:86px;height:86px;border-radius:0 0 43px 43px;display:flex;align-items:center;justify-content:center;font-size:11px;font-weight:600;text-align:center;line-height:13px;padding:6px}
.card h3{margin-top:22px;text-align:center;font-size:14.5px;font-weight:700;text-transform:uppercase}
.card p{margin:10px auto 0;width:260px;text-align:center;font-size:13.5px;line-height:23.5px;color:var(--ink-soft)}
.card a{display:block;margin-top:8px;text-align:center;font-size:13.5px;font-weight:500;text-decoration:underline;color:var(--ocean-deep)}
.arrow{top:1634px;width:32px;height:32px;border-radius:50%;background:var(--ocean);display:flex;align-items:center;justify-content:center}

/* opening */
.opening{left:0;top:1730px;width:1200px;height:710px;background:linear-gradient(180deg,#1493de 0%,#0b7fd0 45%,#1262b8 100%)}
.feature{width:260px;text-align:center;color:var(--white);top:2020px}
.feature h4{margin-top:14px;font-size:19px}
.feature p{margin-top:8px;font-size:13.5px;line-height:23px}
.blob{width:150px;height:98px;margin:0 auto;background:var(--white);border-radius:46% 54% 40% 60%/60% 40% 60% 40%;display:flex;align-items:center;justify-content:center}

/* gallery */
.photo{position:absolute;border-radius:28px}

/* footer */
.site-footer{left:0;top:3235px;width:1200px;height:400px;background:linear-gradient(180deg,#2a1f1b,#171210)}
.col{top:3345px;color:var(--white)}
.col h5{font-family:"Fraunces",serif;font-weight:400;font-size:22px;color:var(--ocean-light);margin-bottom:10px;white-space:nowrap}
.col li{list-style:none;font-size:15px;height:32.5px;display:flex;align-items:center;gap:22px}
.dot{width:13px;height:13px;border-radius:50%;background:var(--white);position:relative}
.dot::after{content:"";position:absolute;left:3px;top:4px;width:3px;height:3px;border-right:1.5px solid #1c1613;border-bottom:1.5px solid #1c1613;transform:rotate(-45deg)}
.email{left:870px;top:3455px;width:214px;height:32px;border-radius:16px;background:var(--white);font-size:10px;color:#888;padding:10px 22px}
.rule{left:111px;top:3585px;width:977px;height:1px;background:rgba(255,255,255,.25)}
.copyright{left:0;width:1200px;top:3606px;text-align:center;font-size:12px;color:var(--white)}
</style>
</head>
<body>

<div class="abs hero" role="img" aria-label="Evening oceanside patio dining with string lights and a city skyline"></div>
<svg class="abs" style="left:0;top:520px" width="1200" height="90" viewBox="0 0 1200 90" aria-hidden="true">
  <path fill="var(--sand)" d="M0,90 L0,40 L35,58 L70,36 L110,54 L150,44 L190,62 L230,40 L280,55 L320,35 L360,50 L410,38 L450,60 L500,42 L540,56 L590,34 L640,52 L690,40 L730,58 L780,38 L830,54 L870,42 L920,60 L970,36 L1010,52 L1060,40 L1100,58 L1150,38 L1200,50 L1200,90 Z"/>
</svg>

<header class="abs site-header">
  <div class="abs brand"><span class="brand-mark"></span>Calloway Food Hall</div>
  <nav class="abs nav">
    <a class="active" href="#">Home</a>
    <a href="#">About Us</a>
    <a href="#">Vendors<span class="caret"></span></a>
    <a href="#">Gallery</a>
    <a href="#">Contact</a>
  </nav>
  <a class="btn reserve" href="#">Make A Reservation</a>
</header>

<div class="abs hero-kicker">Calloway Food Hall</div>
<h1 class="abs hero-title serif">Where Local Flavor Meets<br>Ocean Air</h1>
<a class="btn btn-white" style="left:409px;top:397px;width:184px;height:33px" href="#">Explore Vendors</a>
<a class="btn btn-blue" style="left:607px;top:397px;width:183px;height:33px" href="#">Join Mailing List</a>

<div class="abs story-img" role="img" aria-label="Busy indoor market aisle with produce stalls seen from above"></div>
<h2 class="abs section-title serif" style="left:640px;top:664px">Our Story by the Sea</h2>
<div class="abs story-text">
  <p>Sed ut perspiciatis unde omnis iste natus error sit voluptatem accusantium doloremque laudantium, totam rem aperiam, eaque ipsa quae ab illo inventore veritatis et quasi architecto beatae vitae dicta sunt explicabo.</p>
  <p>Nemo enim ipsam voluptatem quia voluptas sit aspernatur aut odit aut fugit, sed quia consequuntur magni dolores eos qui ratione voluptatem sequi nesciunt.</p>
</div>
<a class="btn btn-blue" style="left:641px;top:974px;width:148px;height:34px" href="#">Explore More</a>

<svg class="abs" style="left:0;top:1040px" width="1200" height="70" viewBox="0 0 1200 70" aria-hidden="true">
  <path fill="none" stroke="var(--sand-pale)" stroke-width="14" stroke-linecap="round" d="M0,40 C120,20 200,55 330,30 C450,8 540,45 660,28 C780,12 900,48 1020,26 C1100,14 1160,30 1200,24"/>
</svg>

<h2 class="abs center section-title serif" style="top:1128px">Taste the Variety</h2>
<div class="abs center sub" style="top:1187px">Ut enim ad minima veniam, quis nostrum exercitationem ullam corporis suscipit</div>

<article class="abs card" style="left:113px">
  <div class="card-photo" role="img" aria-label="Crispy hot chicken with pickles" style="background:linear-gradient(160deg,#d9c9a0,#a8451f 50%,#5a1f10)"></div>
  <div class="card-badge" style="background:#141414;color:var(--white)">Ember Hot Chicken</div>
  <h3>Ember Hot Chicken</h3>
  <p>Quis autem vel eum iure reprehe nde rit qui in ea voluptate velit esse quam nihil molestiae cons</p>
  <a href="#">Explore More</a>
</article>
<article class="abs card featured" style="left:445px">
  <div class="card-photo" role="img" aria-label="Fresh pizza slices on a wooden board" style="background:linear-gradient(160deg,#6b5a48,#c9863f 50%,#2c2a26)"></div>
  <div class="card-badge" style="background:var(--white);color:var(--ink)">Dolce Marea</div>
  <h3>Dolce Marea</h3>
  <p>Quis autem vel eum iure reprehe nde rit qui in ea voluptate velit esse quam nihil molestiae cons</p>
  <a href="#">Explore More</a>
</article>
<article class="abs card" style="left:778px">
  <div class="card-photo" role="img" aria-label="Loaded hot dog with pickles and dipping sauces" style="background:linear-gradient(160deg,#c79a5c,#b43a2a 45%,#8a9a3a 80%)"></div>
  <div class="card-badge" style="background:var(--white);color:var(--ocean-deep)">Orbit Burgers</div>
  <h3>Orbit Burgers</h3>
  <p>Quis autem vel eum iure reprehe nde rit qui in ea voluptate velit esse quam nihil molestiae cons</p>
  <a href="#">Explore More</a>
</article>
<a class="abs arrow" style="left:565px" href="#" aria-label="Previous"><svg width="14" height="12" viewBox="0 0 14 12"><path d="M6,1 L1,6 L6,11 M13,1 L8,6 L13,11" fill="none" stroke="#fff" stroke-width="2"/></svg></a>
<a class="abs arrow" style="left:604px" href="#" aria-label="Next"><svg width="14" height="12" viewBox="0 0 14 12"><path d="M1,1 L6,6 L1,11 M8,1 L13,6 L8,11" fill="none" stroke="#fff" stroke-width="2"/></svg></a>

<div class="abs opening"></div>
<svg class="abs" style="left:0;top:1720px" width="1200" height="60" viewBox="0 0 1200 60" aria-hidden="true">
  <path fill="var(--sand)" d="M0,0 L1200,0 L1200,22 L1160,38 L1110,20 L1060,36 L1010,18 L960,34 L900,16 L850,32 L800,14 L740,30 L690,12 L640,28 L580,10 L530,26 L470,12 L420,30 L360,14 L310,34 L250,16 L200,36 L150,18 L100,40 L50,22 L0,44 Z"/>
</svg>
<svg class="abs" style="left:0;top:2392px" width="1200" height="60" viewBox="0 0 1200 60" aria-hidden="true">
  <path fill="var(--sand)" d="M0,60 L0,30 L40,44 L90,22 L140,42 L190,26 L240,46 L290,28 L340,44 L400,20 L450,40 L500,24 L560,44 L610,26 L660,42 L720,22 L770,40 L820,26 L880,46 L930,24 L980,42 L1040,22 L1090,40 L1140,26 L1200,38 L1200,60 Z"/>
</svg>
<h2 class="abs center serif" style="top:1855px;font-size:42px;color:var(--white)">Opening Summer 2025</h2>
<div class="abs center" style="top:1921px;font-size:15.5px;line-height:31px;color:var(--white)">Ut enim ad minima veniam, quis nostrum exercitationem ullam corporis suscipit<br>vel illum qui dolorem eum fugiat quo voluptas nulla pariatur</div>

<div class="abs feature" style="left:175px">
  <div class="blob"><svg width="48" height="48" viewBox="0 0 48 48" aria-hidden="true"><path d="M14,34 V12 L30,8 V30" fill="none" stroke="#13263a" stroke-width="2.5"/><circle cx="10" cy="34" r="4.5" fill="#13263a"/><circle cx="26" cy="30" r="4.5" fill="var(--ocean)"/><circle cx="38" cy="14" r="2" fill="var(--ocean)"/></svg></div>
  <h4 class="serif">Live Music Nights</h4>
  <p>Ut enim ad minima veniam, quis nostrum exercitationem ullam corpo ris suscipit laboriosam</p>
</div>
<div class="abs feature" style="left:470px">
  <div class="blob"><svg width="48" height="48" viewBox="0 0 48 48" aria-hidden="true"><circle cx="24" cy="16" r="9" fill="var(--ocean)" stroke="#13263a" stroke-width="2"/><path d="M15,20 L24,42 L33,20 Z" fill="none" stroke="#13263a" stroke-width="2.5" stroke-linejoin="round"/></svg></div>
  <h4 class="serif">Kids’ Days</h4>
  <p>Ut enim ad minima veniam, quis nostrum exercitationem ullam corpo ris suscipit laboriosam</p>
</div>
<div class="abs feature" style="left:763px">
  <div class="blob"><svg width="52" height="48" viewBox="0 0 52 48" aria-hidden="true"><circle cx="26" cy="24" r="14" fill="none" stroke="#13263a" stroke-width="2.5"/><circle cx="26" cy="24" r="8" fill="var(--ocean)"/><path d="M6,10 V38 M46,10 V38 M3,10 V18 H9 V10" fill="none" stroke="#13263a" stroke-width="2.5"/></svg></div>
  <h4 class="serif">Chef Pop-Ups</h4>
  <p>Ut enim ad minima veniam, quis nostrum exercitationem ullam corpo ris suscipit laboriosam</p>
</div>
<a class="btn btn-white" style="left:525px;top:2279px;width:148px;height:34px" href="#">Explore More</a>

<h2 class="abs center section-title serif" style="top:2496px">Oceanfront Patio Gallery</h2>
<div class="abs center sub" style="top:2559px">Ut enim ad minima veniam, quis nostrum exercitationem ullam corporis suscipit</div>
<div class="photo" style="left:112px;top:2619px;width:439px;height:243px;background:linear-gradient(120deg,#5a5550,#e8e0d2 40%,#3a3430)" role="img" aria-label="Sushi roll held with chopsticks"></div>
<div class="photo" style="left:575px;top:2619px;width:513px;height:502px;background:linear-gradient(180deg,#6a5a48 0%,#2f8a8a 35%,#b8442e 50%,#4a3a30 75%,#6a6258)" role="img" aria-label="Street-side cafe with colorful umbrellas and outdoor seating"></div>
<div class="abs" style="left:102px;top:2868px;width:620px;height:264px;background:var(--sand);border-radius:0 40px 0 0"></div>
<div class="photo" style="left:112px;top:2880px;width:594px;height:241px;background:linear-gradient(120deg,#2a2420,#c98a3a 45%,#3a2c22)" role="img" aria-label="Grilled chicken skewers with onions"></div>
<a class="btn btn-white" style="left:426px;top:3151px;width:150px;height:34px" href="#">Explore More</a>
<a class="btn btn-blue" style="left:590px;top:3151px;width:184px;height:34px" href="#">Join Mailing List</a>

<footer class="abs site-footer" role="img" aria-label="Dusky ocean shoreline backdrop"></footer>
<svg class="abs" style="left:0;top:3205px" width="1200" height="40" viewBox="0 0 1200 40" aria-hidden="true">
  <path fill="var(--sand)" d="M0,0 L1200,0 L1200,18 L1150,30 L1100,14 L1050,28 L990,12 L940,26 L880,10 L830,28 L770,14 L720,30 L660,12 L610,26 L550,10 L500,28 L440,14 L390,30 L330,12 L280,28 L220,14 L170,32 L110,16 L60,30 L0,18 Z"/>
</svg>
<div class="abs col" style="left:111px"><h5>Quick Links</h5><ul><li><span class="dot"></span>Home</li><li><span class="dot"></span>About Us</li><li><span class="dot"></span>Our Vendors</li><li><span class="dot"></span>Portfolio</li><li><span class="dot"></span>Contact Us</li></ul></div>
<div class="abs col" style="left:354px"><h5>Other Links</h5><ul><li><span class="dot"></span>Vendors</li><li><span class="dot"></span>Events</li><li><span class="dot"></span>Contact Us</li><li><span class="dot"></span>Careers</li></ul></div>
<div class="abs col" style="left:576px"><h5>Share Your Thoughts</h5><ul><li><span class="dot"></span>Facefolio</li><li><span class="dot"></span>Snapgram</li><li><span class="dot"></span>Linkwork</li><li><span class="dot"></span>Viewtube</li><li><span class="dot"></span>Chirper</li></ul></div>
<div class="abs col" style="left:870px;width:225px"><h5>Join the Coastal Club</h5><p style="font-size:14.5px;line-height:27px;width:220px">Quis autem vel eum iure rep rehenderit qui</p></div>
<div class="abs email">Enter Email Address</div>
<a class="btn btn-blue" style="left:870px;top:3500px;width:214px;height:33px" href="#">Keep Me in the Loop</a>
<div class="abs rule"></div>
<div class="abs copyright">(C) Copyright | All Rights Reserved</div>

</body>
</html>
```